Specialised investor in e-mobility and energy wants business card design

We need a business card design that fits our existing corporate design. <The look and feel must be 'sharp'/'clean', dynamic, communicate momentum, professionalism etc (as one would imagine from a firm in the financial sector). We like the idea of a reverse-side of the card that includes the logo, and the name and contact details on the other. We expect the deliverable to be whatever format might be required to be able to get cards printed directly by a service such as kelmo press. Our website is www.zub.capital

```html
<!DOCTYPE html>
<html lang="en">
<head>
<meta charset="utf-8">
<title>ZUB Capital – Business Card</title>
<link rel="stylesheet" href="https://fonts.googleapis.com/css2?family=Lato:wght@400;700;900&display=swap">
<style>
  :root {
    --backdrop: #1d1d1d;
    --card: #ffffff;
    --green-dark: #2f5023;
    --green-light: #86b34a;
    --text-light: #ffffff;
  }
  * { margin: 0; padding: 0; box-sizing: border-box; }
  html, body {
    width: 1200px; height: 1122px; overflow: hidden;
    background: var(--backdrop);
    font-family: "Lato", sans-serif;
  }
  .canvas {
    position: relative; width: 1200px; height: 1122px;
  }
  .card {
    position: absolute; left: 170px;
    width: 860px; height: 490px;
    background: var(--card);
    border-radius: 26px;
    overflow: hidden;
  }
  .card--front { top: 46px; }
  .card--back { top: 586px; }

  .wordmark {
    display: flex; align-items: center; gap: 14px;
    color: var(--green-dark);
    font-weight: 700;
    white-space: nowrap;
  }
  .wordmark__dot {
    width: 0.55em; height: 0.55em;
    border-radius: 50%;
    background: var(--green-light);
  }
  .card--front .wordmark {
    position: absolute; left: 0; right: 0; top: 0; bottom: 0;
    justify-content: center;
    font-size: 84px;
  }
  .card--back .wordmark {
    position: absolute; right: 56px; top: 44px;
    font-size: 50px;
    gap: 10px;
  }

  .person {
    position: absolute; right: 56px; top: 132px;
    text-align: right;
  }
  .person__name {
    font-size: 34px; font-weight: 900;
    color: var(--green-dark);
    line-height: 1.1;
  }
  .person__role {
    font-size: 22px; font-weight: 400;
    color: var(--green-light);
    margin-top: 4px;
  }

  .card__wave {
    position: absolute; left: 0; top: 0;
    width: 860px; height: 490px;
  }

  .contacts {
    position: absolute; left: 150px; top: 342px;
    list-style: none;
    color: var(--text-light);
    font-size: 18px;
    line-height: 1.22;
  }
  .contacts li {
    display: flex; align-items: flex-start; gap: 12px;
    margin-bottom: 3px;
  }
  .contacts svg { flex: none; width: 17px; height: 17px; margin-top: 2px; }
  .contacts__company { font-weight: 700; }
</style>
</head>
<body>
<main class="canvas">

  <section class="card card--front" aria-label="Card front">
    <div class="wordmark"><span class="wordmark__dot"></span>ZUB Capital</div>
  </section>

  <section class="card card--back" aria-label="Card back">
    <svg class="card__wave" viewBox="0 0 860 490" aria-hidden="true">
      <path d="M0 398 C 150 288, 400 258, 860 288 L860 490 L0 490 Z" fill="var(--green-dark)"/>
      <path d="M0 380 C 150 270, 400 240, 860 270" fill="none" stroke="var(--green-light)" stroke-width="10"/>
    </svg>

    <div class="wordmark"><span class="wordmark__dot"></span>ZUB Capital</div>

    <div class="person">
      <p class="person__name">Mark Ellery</p>
      <p class="person__role">Founder &amp; CEO</p>
    </div>

    <ul class="contacts">
      <li>
        <svg viewBox="0 0 24 24"><path d="M12 2a7 7 0 0 0-7 7c0 5 7 13 7 13s7-8 7-13a7 7 0 0 0-7-7zm0 9.5A2.5 2.5 0 1 1 12 6.5a2.5 2.5 0 0 1 0 5z" fill="var(--green-light)"/></svg>
        <span><span class="contacts__company">ZUB Capital S.A.</span><br>Seefeld, Switzerland</span>
      </li>
      <li>
        <svg viewBox="0 0 24 24"><path d="M6.6 10.8a15 15 0 0 0 6.6 6.6l2.2-2.2a1 1 0 0 1 1-.25 11.4 11.4 0 0 0 3.6.6 1 1 0 0 1 1 1V20a1 1 0 0 1-1 1A17 17 0 0 1 3 4a1 1 0 0 1 1-1h3.5a1 1 0 0 1 1 1 11.4 11.4 0 0 0 .6 3.6 1 1 0 0 1-.25 1z" fill="var(--green-light)"/></svg>
        <span>+41 70555 0148</span>
      </li>
      <li>
        <svg viewBox="0 0 24 24"><path d="M3 5h18v14H3z" fill="var(--green-light)"/><path d="M3 5l9 7 9-7" fill="none" stroke="var(--green-dark)" stroke-width="1.6"/></svg>
        <span>mark@zub.capital</span>
      </li>
      <li>
        <svg viewBox="0 0 24 24"><circle cx="12" cy="12" r="9" fill="none" stroke="var(--green-light)" stroke-width="2"/><path d="M3 12h18M12 3c3 3 3 15 0 18M12 3c-3 3-3 15 0 18" fill="none" stroke="var(--green-light)" stroke-width="1.5"/></svg>
        <span>www.zub.capital</span>
      </li>
    </ul>
  </section>

</main>
</body>
</html>
```